2021 Personalized Vision Poster

A beautiful, pleasing design for my 2021 vision poster. Looking probably for an infographic. Open to shortening the wording used if able. As you will notice, each color represents a different category. Let me know if you need more details. The title of each section are mostly listed, but starting with the upper left with “my primary question” going counter-clockwise: my primary question, away values and rules, life purpose, power values (red), toward values and rules, top 4 goals for 2021 (middle), and relationship vision (middle). Basically, I’m just looking for a nice font and different formatting for my words.

Requirements
Must have
• All of the sections with a majority of the words used.
Nice to have
• Infographic would be nice, if possible. More concerned with a beautiful layout of words already expressed.
Should not have
• A complete reworking of the words used.

```html
<!DOCTYPE html>
<html lang="en">
<head>
<meta charset="utf-8">
<title>2021 Vision Poster – Live Courageously</title>
<link href="https://fonts.googleapis.com/css2?family=Lobster&family=Lilita+One&family=Rubik:wght@500;700&family=Amatic+SC:wght@700&family=Oswald:wght@600&display=swap" rel="stylesheet">
<style>
  :root {
    --orange: #f26722;
    --white: #ffffff;
    --script: "Lobster", cursive;
    --hand: "Amatic SC", cursive;
    --block: "Lilita One", sans-serif;
    --body: "Rubik", sans-serif;
    --year: "Oswald", sans-serif;
  }
  * { margin: 0; padding: 0; box-sizing: border-box; }
  html, body { width: 848px; height: 1200px; overflow: hidden; background: var(--white); }
  .poster { position: relative; width: 848px; height: 1200px; overflow: hidden; background: var(--white); }
  .backdrop { position: absolute; inset: 0; }
  .title {
    position: absolute; left: 30px; top: 38px;
    font-family: var(--script); color: var(--orange);
    font-size: 62px; line-height: 0.95; transform: rotate(-11deg); transform-origin: left top;
    font-weight: 400;
  }
  .title span { display: block; }
  .title .line-1 { padding-left: 55px; }
  .year {
    position: absolute; right: 28px; top: -4px;
    font-family: var(--year); font-weight: 600; color: var(--orange);
    font-size: 100px; line-height: 1; letter-spacing: 1px;
  }
  .question {
    position: absolute; left: 46px; top: 258px;
    font-family: var(--hand); font-weight: 700; color: var(--white); font-size: 34px; line-height: 1.25;
    letter-spacing: 1px; text-transform: uppercase;
    transform: rotate(-9.2deg); transform-origin: left top; white-space: nowrap;
  }
  .section-title {
    position: absolute; font-family: var(--script); font-weight: 400; color: var(--white);
    -webkit-text-stroke: 5px var(--orange); paint-order: stroke fill;
    line-height: 0.95; text-align: center;
  }
  .values-title { left: 308px; top: 310px; font-size: 40px; }
  .relationship-title { left: 130px; top: 478px; font-size: 38px; }
  .goals-title { left: 292px; top: 690px; font-size: 44px; }
  .goals-title .sub { display: block; padding-left: 48px; font-size: 36px; }

  .tag {
    position: absolute; height: 19px; border-radius: 4px; background: var(--white); color: var(--orange);
    font-family: var(--body); font-weight: 700; font-size: 12px; text-align: center; line-height: 19px;
  }
  .tag-towards { left: 566px; top: 223px; width: 134px; }
  .tag-avoid { left: 566px; top: 502px; width: 134px; border: 2px solid var(--orange); line-height: 15px; }
  .tag-remember { left: 566px; top: 598px; width: 134px; }

  .rule-list { position: absolute; font-family: var(--body); font-weight: 500; font-size: 13px; line-height: 23px; list-style: none; }
  .towards-list { color: var(--white); top: 250px; left: 0; }
  .towards-list li { position: absolute; white-space: nowrap; }
  .avoid-list { color: var(--orange); left: 494px; top: 526px; }
  .remember-list { color: var(--white); left: 494px; top: 626px; }

  .word-list { position: absolute; list-style: none; font-family: var(--block); color: var(--white); text-transform: uppercase; }
  .relationship-list { left: 60px; top: 630px; font-size: 29px; line-height: 34.5px; text-align: center; width: 170px; }
  .power-list { left: 585px; top: 810px; font-size: 29px; line-height: 41px; }

  .goal-list { position: absolute; left: 262px; top: 812px; font-family: var(--script); color: var(--white); font-size: 38px; line-height: 51px; list-style: none; }
  .goal-list .indent { padding-left: 92px; }

  .purpose {
    position: absolute; left: 20px; top: 1082px; width: 802px; height: 88px; border-radius: 8px;
    background: var(--white); color: var(--orange);
    font-family: var(--hand); font-weight: 700; font-size: 32px; line-height: 37px; letter-spacing: 1px;
    text-transform: uppercase; text-align: center; padding-top: 7px; white-space: nowrap;
  }
</style>
</head>
<body>
<main class="poster">
  <svg class="backdrop" width="848" height="1200" viewBox="0 0 848 1200" aria-hidden="true">
    <path d="M0,232 C260,170 560,112 848,104 L848,1200 L0,1200 Z" fill="var(--orange)"/>
    <path d="M0,246 C260,184 560,126 848,118" fill="none" stroke="var(--white)" stroke-width="3"/>
    <g fill="none" stroke="var(--white)" stroke-width="4">
      <path d="M848,232 H462 A133,133 0 0 0 462,498"/>
      <path d="M462,498 V690 Q462,712 484,712 H848"/>
      <circle cx="422" cy="380" r="72"/>
      <line x1="480" y1="340" x2="555" y2="313"/>
      <path d="M0,402 H262 Q275,402 275,415 V440"/>
      <path d="M275,440 A100,100 0 1 1 212,607"/>
      <path d="M275,615 V730"/>
      <path d="M0,900 H240"/>
      <line x1="522" y1="993" x2="557" y2="993"/>
    </g>
    <rect x="464" y="500" width="384" height="100" fill="var(--white)"/>
    <circle cx="428" cy="378" r="52" fill="var(--white)"/>
    <circle cx="262" cy="520" r="80" fill="var(--white)"/>
    <g fill="var(--white)">
      <circle cx="555" cy="313" r="8"/>
      <circle cx="212" cy="607" r="8"/>
      <circle cx="532" cy="993" r="8"/>
    </g>
    <rect x="238" y="728" width="286" height="310" rx="10" fill="var(--white)"/>
    <rect x="245" y="782" width="272" height="249" rx="6" fill="var(--orange)"/>
    <rect x="556" y="800" width="234" height="260" rx="10" fill="none" stroke="var(--white)" stroke-width="4"/>
  </svg>

  <h1 class="title"><span class="line-1">Live</span><span>Courageously!</span></h1>
  <div class="year">2021</div>

  <p class="question">“How can I be even more grateful for the love in my heart for<br>God, myself and others?”</p>

  <h2 class="section-title values-title">Values &amp;<br>&nbsp;&nbsp;Rules</h2>
  <div class="tag tag-towards">TOWARDS</div>
  <ul class="rule-list towards-list">
    <li style="left:512px;top:0">- Giving of miself and serve others,</li>
    <li style="left:550px;top:23px">- Accepting love from god or others,</li>
    <li style="left:572px;top:46px">- Doing something even when seary,</li>
    <li style="left:584px;top:69px">- Choosing to put myself first,</li>
    <li style="left:592px;top:92px">- Practicing vulnerability,</li>
    <li style="left:596px;top:115px">- Taking actions consistent with</li>
    <li style="left:592px;top:138px">my identity,</li>
    <li style="left:586px;top:161px">- Getting outdoors,</li>
    <li style="left:578px;top:184px">- Going on a little or big adventure,</li>
    <li style="left:564px;top:207px">- Moving my body!</li>
  </ul>
  <div class="tag tag-avoid">AVOID</div>
  <ul class="rule-list avoid-list">
    <li>- Unrighteous anger</li>
    <li>- Debilitating illusion of failure</li>
    <li>- &nbsp;Consisten debilitating Anxiety</li>
  </ul>
  <div class="tag tag-remember">REMEMBER</div>
  <ul class="rule-list remember-list">
    <li>- I alone have the power to choose to be angry</li>
    <li>- God has made me a conqueror - I will not fail</li>
    <li>- God has given me all the inner peace i need</li>
  </ul>

  <h2 class="section-title relationship-title">Relationship<br>&nbsp;&nbsp;Vision</h2>
  <ul class="word-list relationship-list">
    <li>- Love</li><li>- Respect</li><li>-Courage</li><li>- Fun</li><li>-Flirty</li><li>- Romantic</li><li>-Desire</li>
  </ul>

  <h2 class="section-title goals-title">Top 4<span class="sub">Goals</span></h2>
  <ol class="goal-list">
    <li>1-Rental</li>
    <li class="indent">2-175 lbs</li>
    <li>3 -Team</li>
    <li class="indent">4 -$250K</li>
  </ol>

  <ul class="word-list power-list">
    <li>- Pow</li><li>- Courage</li><li>- Love</li><li>- ER</li><li>- Joy</li><li>- Presence</li>
  </ul>

  <p class="purpose">The purpose of my life is to be loving courageous, and fun! I seek<br>adventure, laugh and play, and libe in God’s identity for me.</p>
</main>
</body>
</html>
```